American cannabis tech company business card design

Pavrel.com is seeking a modern, professional, and brand-aligned business card that represents our company and its core values: Mission, Story, Values, and Impact. As an innovative cannabis company, we want a business card that is not only visually appealing but also serves as a representation of who we are and what we stand for.

Project Scope: Design a double-sided business card that integrates our brand identity and core values. Incorporate our key brand elements, ensuring a sleek and contemporary aesthetic. Visually reflect our core values (Mission, Story, Values, Impact) in a way that is engaging yet professional.

Target Market(s)

Vendors, third parties,

Contact Information for Business Card

Contact details (name, title, email, phone, website, etc.)

Font styles to use
Other font styles liked:
• Caslon, Centra

Colors

Designer to choose colors to be used in the design.

Requirements
Must have
• Pavrel.com logo and branding A creative yet clean way to integrate our core values (Mission, Story, Values, Impact) Modern typography and a well-structured layout
Nice to have
• forest green, grey, white, black
Should not have
• references to marijuana, leafs, plants, or related product

```html
<!DOCTYPE html>
<html lang="en">
<head>
<meta charset="utf-8">
<title>Pavrel.com Business Card</title>
<link rel="stylesheet" href="https://fonts.googleapis.com/css2?family=Poppins:wght@300;400;600;800&display=swap">
<style>
  :root {
    --page-bg: #d8d1c7;
    --frost-light: #f4f4f2;
    --frost-mid: #d9dcdc;
    --frost-shade: #c4c8c8;
    --ink: #121614;
    --panel-dark: #1a1c1b;
    --panel-deep: #0d0f0e;
    --band: #1e2923;
    --silver: #e6e3df;
    --rose: #d6b0a2;
    --muted: #8f8a85;
    --web: #a39e99;
  }
  html, body {
    margin: 0;
    padding: 0;
    width: 1200px;
    height: 970px;
    overflow: hidden;
    background: var(--page-bg);
    font-family: "Poppins", sans-serif;
  }
  .card {
    position: absolute;
    left: 100px;
    top: 201px;
    width: 1000px;
    height: 568px;
    border-radius: 26px;
    overflow: hidden;
    box-shadow: 0 18px 40px rgba(0,0,0,0.18);
  }
  .card svg { display: block; }
  .brand-name { font-weight: 800; font-size: 122px; fill: var(--ink); letter-spacing: -2px; }
  .person-name { font-weight: 600; font-size: 27px; fill: #ecd9d0; }
  .person-title { font-weight: 400; font-size: 22px; fill: var(--rose); }
  .contact-line { font-weight: 300; font-size: 23px; }
  .contact-phone { fill: var(--muted); }
  .contact-email { fill: #c9aaa0; }
  .website { font-weight: 400; font-size: 21px; fill: var(--web); letter-spacing: 12px; }
</style>
</head>
<body>
<div class="card">
  <svg width="1000" height="568" viewBox="0 0 1000 568" xmlns="http://www.w3.org/2000/svg">
    <defs>
      <linearGradient id="frost" x1="0" y1="0" x2="1" y2="0">
        <stop offset="0" stop-color="var(--frost-mid)"/>
        <stop offset="0.35" stop-color="var(--frost-light)"/>
        <stop offset="0.6" stop-color="var(--frost-shade)"/>
        <stop offset="0.85" stop-color="var(--frost-light)"/>
        <stop offset="1" stop-color="var(--frost-mid)"/>
      </linearGradient>
      <linearGradient id="panel" x1="0" y1="0" x2="0" y2="1">
        <stop offset="0" stop-color="var(--panel-dark)"/>
        <stop offset="1" stop-color="var(--panel-deep)"/>
      </linearGradient>
    </defs>

    <rect class="card-face" width="1000" height="568" fill="url(#frost)"/>

    <text class="brand-name" x="500" y="216" text-anchor="middle">PAVREL</text>

    <path class="silver-arc" d="M0 176 Q500 468 1000 176" fill="none" stroke="var(--silver)" stroke-width="3"/>
    <path class="dark-swoosh" d="M0 184 Q500 470 1000 184 L1000 191 Q500 487 0 191 Z" fill="var(--band)"/>
    <path class="info-panel" d="M0 191 Q500 487 1000 191 L1000 568 L0 568 Z" fill="url(#panel)"/>

    <text class="person-name" x="479" y="421" text-anchor="end">DANIEL R. HAYES</text>
    <text class="person-title" x="479" y="452" text-anchor="end">Director</text>

    <rect class="divider" x="501" y="400" width="2" height="54" fill="var(--rose)"/>

    <g class="icon-phone" transform="translate(530 412)">
      <circle r="12" fill="var(--rose)"/>
      <path d="M-5 -6 l3 -1 2 4 -2 1.5 q1.5 3 4 4.5 l1.5 -2 4 2 -1 3 q-6 0 -11.5 -12 z" fill="var(--panel-dark)"/>
    </g>
    <text class="contact-line contact-phone" x="552" y="421">+1 555-218-4390</text>

    <g class="icon-email" transform="translate(530 444)">
      <circle r="12" fill="var(--rose)"/>
      <rect x="-6.5" y="-4.5" width="13" height="9" fill="none" stroke="var(--panel-dark)" stroke-width="1.6"/>
      <path d="M-6.5 -4.5 L0 1 L6.5 -4.5" fill="none" stroke="var(--panel-dark)" stroke-width="1.6"/>
    </g>
    <text class="contact-line contact-email" x="552" y="453">team@pavrel.com</text>

    <rect class="silver-rule" x="0" y="510" width="1000" height="4" fill="var(--silver)" opacity="0.8"/>
    <rect class="web-band" x="0" y="514" width="1000" height="54" fill="var(--band)"/>
    <text class="website" x="500" y="549" text-anchor="middle">www.PAVREL.com</text>
  </svg>
</div>
</body>
</html>
```